Business Card Design for Training Business

Clear Path Coaching is a new business that delivers training and other services with a focus on topics related to mental health and wellbeing, for example, Wellmind Response Course, Resilience etc. We have a strong focus on evidence-based psychology and neuroscience. I have a logo which I will upload with the brief, so please consider colours that work well with the logo.
Target Market(s)
Adults, workplaces (particularly government and not-for-profits)
Industry/Entity Type
Business
Contact Information for Business Card
Head Strong TrainingSamantha SellwoodDirector0438 770 850sam@headstrongtraining.com.auwww.headstrongtraining.com.au

```html
<!DOCTYPE html>
<html lang="en">
<head>
<meta charset="utf-8">
<title>Clear Path Coaching – Business Card</title>
<link rel="stylesheet" href="https://fonts.googleapis.com/css2?family=Open+Sans:wght@300;400;600&display=swap">
<style>
  :root {
    --bg: #e9e7e4;
    --card: #fbfbfa;
    --teal: #5fc1d4;
    --teal-line: #6cc7d6;
    --taupe: #8e7f78;
    --ink: #1c1c1c;
    --logo-grey: #9a8f8b;
  }
  * { box-sizing: border-box; margin: 0; padding: 0; }
  html, body {
    width: 1200px; height: 892px; overflow: hidden;
    background: var(--bg);
    font-family: "Open Sans", sans-serif;
  }
  .canvas {
    width: 1200px; height: 892px;
    display: flex; align-items: center; justify-content: center;
  }
  .card {
    position: relative;
    width: 1050px; height: 600px;
    background: var(--card);
    box-shadow: 0 12px 30px rgba(0,0,0,0.15);
    overflow: hidden;
  }
  .card-band {
    position: absolute; inset: 0;
    width: 100%; height: 100%;
  }
  .brand {
    position: absolute;
    left: 40px; top: 110px; width: 400px;
    display: flex; flex-direction: column; align-items: center;
  }
  .brand-mark {
    width: 150px; height: 150px;
    border-radius: 50%;
    border: 3px solid var(--teal);
    margin-bottom: 28px;
  }
  .brand-name {
    font-weight: 300;
    color: var(--logo-grey);
    font-size: 34px;
    letter-spacing: 3px;
    text-transform: uppercase;
    text-align: center;
    line-height: 1.25;
  }
  .divider {
    position: absolute;
    left: 470px; top: 70px;
    width: 2px; height: 380px;
    background: var(--teal-line);
  }
  .contact {
    position: absolute;
    left: 515px; top: 88px;
    color: var(--ink);
  }
  .contact-name {
    font-weight: 600;
    font-size: 40px;
    line-height: 1.1;
  }
  .contact-role {
    font-size: 30px;
    font-weight: 400;
    margin-bottom: 26px;
  }
  .contact-list { list-style: none; }
  .contact-item {
    display: flex; align-items: center;
    font-size: 28px;
    line-height: 1.55;
  }
  .contact-icon {
    width: 24px; height: 24px;
    margin-right: 14px;
    flex: none;
  }
</style>
</head>
<body>
<main class="canvas">
  <article class="card">
    <svg class="card-band" viewBox="0 0 1050 600" preserveAspectRatio="none" aria-hidden="true">
      <path fill="var(--taupe)" d="M0 500 C 280 500, 520 515, 660 430 C 780 355, 920 330, 1050 322 L1050 600 L0 600 Z"/>
      <path fill="var(--teal)" d="M0 518 C 280 518, 530 533, 672 448 C 792 373, 930 348, 1050 340 L1050 600 L0 600 Z"/>
    </svg>

    <div class="brand">
      <div class="brand-mark"></div>
      <div class="brand-name">Clear Path Coaching</div>
    </div>

    <div class="divider"></div>

    <section class="contact">
      <h1 class="contact-name">Rebecca Tanfield</h1>
      <p class="contact-role">Director</p>
      <ul class="contact-list">
        <li class="contact-item">
          <svg class="contact-icon" viewBox="0 0 24 24" aria-hidden="true">
            <rect width="24" height="24" rx="3" fill="var(--ink)"/>
            <path fill="#fff" d="M7 5 L10 5 L11 9 L9 10.5 C10 13 11 14 13.5 15 L15 13 L19 14 L19 17 C19 18 18 19 17 19 C10 19 5 14 5 7 C5 6 6 5 7 5 Z"/>
          </svg>
          <span>0491 362 517</span>
        </li>
        <li class="contact-item">
          <svg class="contact-icon" viewBox="0 0 24 24" aria-hidden="true">
            <rect width="24" height="24" rx="3" fill="var(--ink)"/>
            <rect x="4.5" y="7" width="15" height="10" fill="none" stroke="#fff" stroke-width="1.6"/>
            <path d="M4.5 7 L12 13 L19.5 7" fill="none" stroke="#fff" stroke-width="1.6"/>
          </svg>
          <span>bec@clearpathcoaching.example.au</span>
        </li>
        <li class="contact-item">
          <svg class="contact-icon" viewBox="0 0 24 24" aria-hidden="true">
            <rect width="24" height="24" rx="3" fill="var(--ink)"/>
            <circle cx="12" cy="12" r="7" fill="none" stroke="#fff" stroke-width="1.6"/>
            <ellipse cx="12" cy="12" rx="3" ry="7" fill="none" stroke="#fff" stroke-width="1.3"/>
            <path d="M5 12 H19" stroke="#fff" stroke-width="1.3"/>
          </svg>
          <span>www.clearpathcoaching.example.au</span>
        </li>
      </ul>
    </section>
  </article>
</main>
</body>
</html>
```